Business Cards - New Logo Rebranding

Hello We know have a red and blue logo and are looking to create new cards. We are looking for the best creativity of the new logo merged with some of the existing artwork provided.

Target Market(s)

Realtors

Industry/Entity Type

Real Estate

Contact Information for Business Card

New logo with rebranded colors

Requirements
Must have
• Creative use of the new logo

```html
<!DOCTYPE html>
<html lang="en">
<head>
<meta charset="utf-8">
<title>Summit Crest Business Cards</title>
<link href="https://fonts.googleapis.com/css2?family=Tinos:wght@400;700&display=swap" rel="stylesheet">
<style>
  :root {
    --backdrop: #e4e5e7;
    --paper: #ffffff;
    --brand-blue: #3a8fdc;
    --brand-red: #ee5565;
    --ink: #1e1e1e;
    --teal-light: #2aa6d3;
    --teal-dark: #1d5a70;
  }
  html, body {
    margin: 0;
    width: 1200px;
    height: 1200px;
    overflow: hidden;
    background: var(--backdrop);
    font-family: "Tinos", "Times New Roman", serif;
  }
  .card {
    position: absolute;
    left: 180px;
    width: 840px;
    height: 480px;
    border-radius: 36px;
    overflow: hidden;
  }
  .card-front { top: 90px; background: var(--paper); }
  .card-back {
    top: 630px;
    background: linear-gradient(120deg, var(--teal-light) 0%, #237f9f 50%, var(--teal-dark) 100%);
  }
  .accent-block { position: absolute; left: 0; top: 110px; width: 34px; height: 60px; background: var(--brand-red); }
  .band-blue { position: absolute; left: 0; bottom: 0; width: 460px; height: 62px; background: var(--brand-blue); }
  .band-red { position: absolute; left: 485px; bottom: 0; width: 355px; height: 80px; background: var(--brand-red); }
  .divider { position: absolute; left: 405px; top: 100px; width: 2px; height: 210px; background: var(--brand-red); }

  .brand {
    position: absolute;
    display: flex;
    align-items: center;
    gap: 16px;
  }
  .brand-front { left: 60px; top: 150px; }
  .brand-mark {
    border-radius: 50%;
    border: 5px solid var(--brand-red);
    box-sizing: border-box;
  }
  .brand-front .brand-mark { width: 96px; height: 96px; }
  .brand-name {
    font-weight: 700;
    font-size: 36px;
    color: var(--brand-blue);
    white-space: nowrap;
  }

  .person { position: absolute; left: 450px; top: 100px; }
  .person-name { margin: 0; font-size: 34px; font-weight: 400; line-height: 40px; color: var(--ink); }
  .person-name .first { color: var(--brand-red); font-weight: 700; }
  .person-title {
    margin: 4px 0 0;
    padding-bottom: 6px;
    font-size: 26px;
    color: var(--ink);
    border-bottom: 2px solid var(--brand-blue);
    display: inline-block;
  }
  .icon-pill {
    position: absolute;
    left: 620px; top: 206px;
    width: 150px; height: 34px;
    border-radius: 17px;
    background: var(--brand-blue);
    display: flex;
    justify-content: space-around;
    align-items: center;
  }
  .icon-pill svg { width: 18px; height: 18px; }
  .contacts {
    position: absolute;
    left: 450px; top: 250px;
    margin: 0; padding: 0; list-style: none;
    font-size: 24px;
    line-height: 30px;
    color: var(--ink);
  }
  .contacts .phone { padding-left: 170px; }

  .brand-back { left: 50%; top: 150px; transform: translateX(-50%); }
  .brand-back .brand-mark { width: 130px; height: 130px; border-color: var(--brand-red); }
  .brand-back .brand-name { font-size: 46px; color: var(--brand-red); }
  .services {
    position: absolute;
    left: 140px; top: 330px;
    width: 560px; height: 40px;
    border-radius: 20px;
    background: var(--paper);
    color: var(--brand-red);
    font-size: 20px;
    line-height: 40px;
    text-align: center;
    letter-spacing: 0.5px;
  }
</style>
</head>
<body>
  <section class="card card-front">
    <div class="accent-block"></div>
    <div class="band-blue"></div>
    <div class="band-red"></div>
    <div class="brand brand-front">
      <div class="brand-mark"></div>
      <span class="brand-name">Summit Crest</span>
    </div>
    <div class="divider"></div>
    <div class="person">
      <h1 class="person-name"><span class="first">Dana</span> Whitford</h1>
      <p class="person-title">Certified Mold Inspector</p>
    </div>
    <div class="icon-pill">
      <svg viewBox="0 0 24 24" aria-label="phone"><path d="M6 2h4l2 5-3 2a12 12 0 0 0 6 6l2-3 5 2v4a2 2 0 0 1-2 2A18 18 0 0 1 4 4a2 2 0 0 1 2-2z" fill="none" stroke="#ee5565" stroke-width="2"/></svg>
      <svg viewBox="0 0 24 24" aria-label="email"><circle cx="12" cy="12" r="4" fill="none" stroke="#ee5565" stroke-width="2"/><path d="M16 12v2a3 3 0 0 0 6 0v-2a10 10 0 1 0-4 8" fill="none" stroke="#ee5565" stroke-width="2"/></svg>
      <svg viewBox="0 0 24 24" aria-label="web"><rect x="3" y="5" width="18" height="14" fill="none" stroke="#ee5565" stroke-width="2"/><path d="M3 6l9 7 9-7" fill="none" stroke="#ee5565" stroke-width="2"/></svg>
    </div>
    <ul class="contacts">
      <li class="phone">800.555.0142</li>
      <li class="phone">562.555.0198</li>
      <li>dana@summitcrestinspect.com</li>
      <li>www.SummitCrestInspect.com</li>
    </ul>
  </section>

  <section class="card card-back">
    <div class="brand brand-back">
      <div class="brand-mark"></div>
      <span class="brand-name">Summit Crest</span>
    </div>
    <div class="services">HOME.SEWER.MOLD.COMMERCIAL.TERMITE.ROOF</div>
  </section>
</body>
</html>
```